Vantrel System Web Page Design

This project is to design 6 pages of a web based medical system for clinics, hospitals, drugs suppliers, general items suppliers, insurance company, laboratories and patients (basically all parties which could be involved in).We want the designs of the browser, button, icon and layout are based on Zeltor, which is user friendly, looks professional, simple and neat but with powerful functions. We have uploaded few pictures of another system, please do not copy its design because this is not what we are looking for, the pictures are for you to know the elements should be included in our pages. Vantrel web-base system, design 6 pages1. Login PageShould include the following elements-company id with input field-login id with input field-password with input field2. Main Page (Navigation page)Should include the following elements-Appointment-Consultation-Patient-Drugs inventory -General supplies inventory -Laboratory-Suppliers-Insurance-Reports 3. Appointment PageShould include all the the elements in the respective pictures plus the followings-Daily View, Weekly View, Monthly View buttons4. Consultation PageShould include all the the elements in the respective picture5. Patient Page5.1 General information Should include all the the elements in the respective picture5.2 medical history/lab reportsShould include all the the elements in the respective picture plus the followings-Notify patient button-Share report button.
Updated on 28 Nov:
Please stop using Harbor Suite in your designs which is not the name of our system. We have just rename our system to Vantrel, please take note.
We need the system to look professional not playful, do not use too many colors and playful icons.

```html
<!DOCTYPE html>
<html lang="en">
<head>
<meta charset="utf-8">
<title>Harbor Suite – System Screens</title>
<link href="https://fonts.googleapis.com/css2?family=Open+Sans:wght@400;600;700;800&display=swap" rel="stylesheet">
<style>
:root{
  --stage:#efefef;
  --white:#ffffff;
  --navy:#26259a;
  --navy-dark:#1f1f86;
  --red:#dc2f2f;
  --ink:#333333;
  --muted:#777777;
  --line:#cfcfd6;
  --grad-a:#c9404a;
  --grad-b:#8a3a78;
  --grad-c:#4b33a6;
}
*{box-sizing:border-box;margin:0;padding:0}
html,body{width:1200px;height:474px;overflow:hidden;background:var(--stage);font-family:"Open Sans",sans-serif;color:var(--ink)}
.stage{position:relative;width:1200px;height:474px}
.panel{position:absolute;top:67px;width:325px;background:var(--white);box-shadow:0 1px 4px rgba(0,0,0,.12);overflow:hidden}
.abs{position:absolute}

/* brand */
.brand{position:absolute;display:flex;align-items:center;gap:4px;font-weight:800;color:var(--navy);font-size:13px;letter-spacing:-.2px;white-space:nowrap}
.brand .dot{width:9px;height:9px;border-radius:50%;background:var(--red)}

/* shared header */
.top-tools{position:absolute;right:14px;top:13px;display:flex;align-items:center;gap:9px;font-size:5.5px}
.lang{display:flex;align-items:center;gap:3px}
.lang i{width:5px;height:5px;border:0.6px solid #999;border-radius:50%;display:inline-block}
.exit-btn{background:var(--navy);color:#fff;border-radius:8px;padding:2.5px 11px;font-size:5.5px;font-weight:600}

.footer{position:absolute;left:0;right:0;height:17px;background:var(--navy);color:#e8e8ff;font-size:3.8px;display:flex;align-items:center;justify-content:space-between;padding:0 29px}

/* login */
.login{left:58px;height:322px}
.login-bg{position:absolute;inset:0;background:linear-gradient(160deg,var(--grad-a) 0%,var(--grad-b) 48%,var(--grad-c) 100%)}
.login-card{position:absolute;left:82px;top:39px;width:160px;height:245px;background:rgba(255,255,255,.93);text-align:center}
.login-card .brand{left:0;right:0;top:21px;justify-content:center;font-size:12px}
.nav-arrow{position:absolute;top:23px;width:11px;height:11px;border:0.7px solid #bbb;border-radius:50%;font-size:6px;line-height:10px;color:#999}
.login-title{position:absolute;left:0;right:0;top:61px;color:var(--red);font-size:13px;font-weight:700}
.login-text{position:absolute;left:18px;right:18px;top:80px;font-size:4.6px;line-height:8px;color:var(--muted)}
.field{position:absolute;left:20px;width:119px;height:20px;background:#fff;border:0.7px solid #d6d6d6;font-size:6px;color:#999;text-align:left;padding-left:7px;line-height:19px}
.field i{position:absolute;right:4px;top:3.5px;width:12px;height:12px;border:0.6px solid #bbb;border-radius:50%;font-style:normal;font-size:5px;line-height:11px;text-align:center}
.login-btn{position:absolute;left:20px;top:193px;width:119px;height:18px;background:var(--navy);color:#fff;font-size:6px;font-weight:700;line-height:18px}

/* main menu */
.menu{left:434px;height:278px}
.menu .brand{left:30px;top:22px}
.tile{position:absolute;width:50px;height:69px;background:#fff;box-shadow:0 0 3px rgba(0,0,0,.15);text-align:center}
.tile svg{position:absolute;left:13px;top:8px}
.tile-label{position:absolute;left:2px;right:2px;top:35px;font-size:4.2px;font-weight:700;line-height:5.5px}
.tile-btn{position:absolute;left:9px;width:32px;top:52px;height:9px;border-radius:5px;background:var(--navy);color:#fff;font-size:3.6px;line-height:9px;font-weight:600}

/* record page */
.record{left:812px;height:338px}
.record .brand{left:30px;top:14px}
.tabbar{position:absolute;left:0;right:0;top:38px;height:13px;background:var(--red);display:flex;justify-content:center;gap:8px;color:#fff;font-size:4.4px;align-items:center}
.box{position:absolute;background:#fff;border:0.7px solid var(--line);font-size:5px;line-height:8px;color:#555}
.box p{position:absolute;left:6px;right:10px}
.scroll{position:absolute;right:0;top:0;bottom:0;width:5px;border-left:0.6px solid #e0e0e0}
.pill{display:inline-block;border:0.7px solid var(--navy);color:var(--navy);border-radius:5px;height:9px;line-height:8px;font-size:3.4px;text-align:center;font-weight:600}
.pill-row{position:absolute;display:flex;gap:3px}
.view-btn{position:absolute;right:3px;top:4px;width:24px;height:9px;border-radius:5px;background:var(--navy);color:#fff;font-size:3.8px;text-align:center;line-height:9px;font-weight:700}
.select{position:absolute;left:3px;top:5px;width:50px;height:8px;border:0.6px solid #ccc}
.date-head{position:absolute;left:0;right:0;top:0;height:12px;background:var(--red);color:#fff;font-size:4.4px;font-weight:700;line-height:12px;padding-left:9px}
.entry-title{color:var(--navy);font-weight:700;font-size:4.4px}
.entry-sub{font-size:4.1px;color:#666}
</style>
</head>
<body>
<div class="stage">

  <!-- Login screen -->
  <section class="panel login">
    <div class="login-bg" role="img" aria-label="Soft medical photo behind a red to purple gradient"></div>
    <div class="login-card">
      <span class="nav-arrow" style="left:10px">&larr;</span>
      <span class="nav-arrow" style="right:10px">&rarr;</span>
      <div class="brand"><span>Harbor Suite</span><span class="dot"></span></div>
      <h1 class="login-title">Harbor Suite</h1>
      <p class="login-text">At vero eos et accusamus et iusto odio dignissimos ducimus qui blanditiis praesentium</p>
      <div class="field" style="top:113px">Company id<i>&darr;</i></div>
      <div class="field" style="top:140px">Login id<i>&darr;</i></div>
      <div class="field" style="top:166px">Password<i>&darr;</i></div>
      <div class="login-btn">LOGIN NOW</div>
    </div>
  </section>

  <!-- Main navigation screen -->
  <section class="panel menu">
    <div class="brand"><span>Harbor Suite</span><span class="dot"></span></div>
    <div class="top-tools"><span class="lang">English <i></i></span><span class="exit-btn">Exit</span></div>

    <div class="tile" style="left:30px;top:77px">
      <svg width="24" height="24" viewBox="0 0 24 24"><circle cx="12" cy="12" r="11.5" fill="none" stroke="#333" stroke-width=".8"/><rect x="7" y="8" width="10" height="9" fill="none" stroke="#26259a" stroke-width=".8"/><line x1="7" y1="11" x2="17" y2="11" stroke="#dc2f2f" stroke-width=".8"/></svg>
      <div class="tile-label">APPOINTMENT</div><div class="tile-btn">VIEW INFO</div></div>
    <div class="tile" style="left:84px;top:77px">
      <svg width="24" height="24" viewBox="0 0 24 24"><circle cx="12" cy="12" r="11.5" fill="none" stroke="#333" stroke-width=".8"/><circle cx="12" cy="9" r="2.5" fill="none" stroke="#26259a" stroke-width=".8"/><path d="M7 17q5-6 10 0" fill="none" stroke="#dc2f2f" stroke-width=".8"/></svg>
      <div class="tile-label">CONSULTATION</div><div class="tile-btn">VIEW INFO</div></div>
    <div class="tile" style="left:138px;top:77px">
      <svg width="24" height="24" viewBox="0 0 24 24"><circle cx="12" cy="12" r="11.5" fill="none" stroke="#333" stroke-width=".8"/><rect x="8" y="7" width="8" height="10" fill="none" stroke="#26259a" stroke-width=".8"/><path d="M12 10v4M10 12h4" stroke="#dc2f2f" stroke-width=".8"/></svg>
      <div class="tile-label">PATIENT</div><div class="tile-btn">VIEW INFO</div></div>
    <div class="tile" style="left:191px;top:77px">
      <svg width="24" height="24" viewBox="0 0 24 24"><circle cx="12" cy="12" r="11.5" fill="none" stroke="#333" stroke-width=".8"/><rect x="9" y="7" width="6" height="10" rx="1" fill="none" stroke="#26259a" stroke-width=".8"/><line x1="9" y1="10" x2="15" y2="10" stroke="#dc2f2f" stroke-width=".8"/></svg>
      <div class="tile-label">DRUGS INVENTORY</div><div class="tile-btn">VIEW INFO</div></div>
    <div class="tile" style="left:245px;top:77px">
      <svg width="24" height="24" viewBox="0 0 24 24"><circle cx="12" cy="12" r="11.5" fill="none" stroke="#333" stroke-width=".8"/><rect x="7" y="7" width="10" height="10" fill="none" stroke="#26259a" stroke-width=".8"/><path d="M7 12h10M12 7v10" stroke="#dc2f2f" stroke-width=".6"/></svg>
      <div class="tile-label">GENERAL SUPPLIES INVENTORY</div><div class="tile-btn">VIEW INFO</div></div>

    <div class="tile" style="left:58px;top:159px">
      <svg width="24" height="24" viewBox="0 0 24 24"><circle cx="12" cy="12" r="11.5" fill="none" stroke="#333" stroke-width=".8"/><path d="M10 6h4M11 6v5l-4 6h10l-4-6V6" fill="none" stroke="#26259a" stroke-width=".8"/></svg>
      <div class="tile-label">LABORATORY</div><div class="tile-btn">VIEW INFO</div></div>
    <div class="tile" style="left:112px;top:159px">
      <svg width="24" height="24" viewBox="0 0 24 24"><circle cx="12" cy="12" r="11.5" fill="none" stroke="#333" stroke-width=".8"/><rect x="6" y="9" width="12" height="8" fill="none" stroke="#26259a" stroke-width=".8"/><path d="M12 11v4M10 13h4" stroke="#dc2f2f" stroke-width=".8"/></svg>
      <div class="tile-label">SUPPLIERS</div><div class="tile-btn">VIEW INFO</div></div>
    <div class="tile" style="left:166px;top:159px">
      <svg width="24" height="24" viewBox="0 0 24 24"><circle cx="12" cy="12" r="11.5" fill="none" stroke="#333" stroke-width=".8"/><rect x="8" y="6" width="8" height="11" fill="none" stroke="#26259a" stroke-width=".8"/><path d="M10 10h4M10 12h4M10 14h3" stroke="#dc2f2f" stroke-width=".6"/></svg>
      <div class="tile-label">INSURANCE</div><div class="tile-btn">VIEW INFO</div></div>
    <div class="tile" style="left:218px;top:159px">
      <svg width="24" height="24" viewBox="0 0 24 24"><circle cx="12" cy="12" r="11.5" fill="none" stroke="#333" stroke-width=".8"/><rect x="8" y="6" width="8" height="12" fill="none" stroke="#26259a" stroke-width=".8"/><path d="M10 15v-2M12 15v-4M14 15v-3" stroke="#dc2f2f" stroke-width=".8"/></svg>
      <div class="tile-label">REPORTS</div><div class="tile-btn">VIEW INFO</div></div>

    <footer class="footer" style="top:262px"><span>Copyrights© 2018 . All Rights Reserved.</span><span>SUPPORT HOTLINE : (555) 0142 7710</span></footer>
  </section>

  <!-- Patient record screen -->
  <section class="panel record">
    <div class="brand"><span>Harbor Suite</span><span class="dot"></span></div>
    <div class="top-tools" style="top:15px"><span class="lang">English <i></i></span><span class="exit-btn">Exit</span></div>
    <nav class="tabbar"><span>ALLERGY</span><span>MEDICAL HIS.</span><span>IMMUNIZATION</span><span>GLUCOSE DATA H</span><span>BP DATA G</span><span>LABORATORY</span><span>IMAGE. DOC.</span><span>OTHERS</span></nav>

    <div class="box" style="left:29px;top:65px;width:83px;height:85px">
      <p style="top:5px">At vero eos et accusamus et iusto odio dignissimos ducim qui blanditiis praesentium voluptatum deleniti</p>
      <div class="scroll" style="bottom:18px"></div>
      <div class="pill-row" style="left:4px;top:70px"><span class="pill" style="width:24px">ADD</span><span class="pill" style="width:24px">EDIT</span><span class="pill" style="width:24px">DELETE</span></div>
    </div>
    <div class="box" style="left:121px;top:65px;width:83px;height:85px">
      <div class="select"></div><div class="view-btn">VIEW</div>
      <p style="top:22px">At vero eos et accusamus et iusto odio dignissimos ducim qui blanditiis praesentium voluptatum deleniti</p>
      <div class="scroll" style="top:18px"></div>
    </div>
    <div class="box" style="left:213px;top:65px;width:83px;height:85px">
      <p style="top:5px">At vero eos et accusamus et iusto odio dignissimos ducim qui blanditiis praesentium voluptatum deleniti</p>
      <div class="scroll" style="bottom:18px"></div>
      <div class="pill-row" style="left:4px;top:70px"><span class="pill" style="width:24px">ADD</span><span class="pill" style="width:24px">LABEL</span><span class="pill" style="width:24px">DELETE</span></div>
    </div>

    <div class="box" style="left:30px;top:162px;width:163px;height:137px">
      <div class="date-head">JUNE 28, 2010</div>
      <p style="top:19px;right:80px">At vero eos et accusamus et iusto odio dignissimos ducim qui blanditiis praesentium voluptatum deleniti</p>
    </div>
    <div class="box" style="left:200px;top:162px;width:96px;height:137px">
      <div class="date-head">JUNE 28, 2010</div>
      <p style="top:18px;line-height:9.3px">
        <span class="entry-title">AT VERO EOS ET ACCUSAMUS ET</span><br>
        <span class="entry-sub">iusto odio dignissimos ducim</span><br>
        <span class="entry-title">QUI BLANDITIIS PRAESENTIUM</span><br>
        <span class="entry-sub">voluptatum deleniti</span><br>
        <span class="entry-title">AT VERO EOS ET ACCUSAMUS ET</span><br>
        <span class="entry-sub">iusto odio dignissimos ducim</span>
      </p>
    </div>

    <div class="pill-row" style="left:31px;top:310px;gap:4px">
      <span class="pill" style="width:24px;height:11px;line-height:10px">NEXT</span>
      <span class="pill" style="width:24px;height:11px;line-height:10px">APPOINT</span>
      <span class="pill" style="width:24px;height:11px;line-height:10px">SEARCH</span>
      <span class="pill" style="width:24px;height:11px;line-height:10px">PATIENT</span>
      <span class="pill" style="width:24px;height:11px;line-height:10px">RECALL</span>
      <span class="pill" style="width:24px;height:11px;line-height:10px">BILL DOC</span>
      <span class="pill" style="width:30px;height:11px;line-height:10px">DOCUMENT</span>
      <span class="pill" style="width:24px;height:11px;line-height:10px">WRITE</span>
      <span class="pill" style="width:24px;height:11px;line-height:10px">PRINT</span>
      <span class="pill" style="width:24px;height:11px;line-height:10px">MAIN</span>
    </div>

    <footer class="footer" style="top:322px;height:16px"><span>Copyrights© 2018 . All Rights Reserved.</span><span>SUPPORT HOTLINE : (555) 0142 7710</span></footer>
  </section>

</div>
</body>
</html>
```